Website for Vornelix Capital, my new firm that raises money from investors to buy, build, own an...

Vornelix Capital needs a website! We are a new company with very experienced people, who invest in, own and build hotel properties, as well as apartments and other commercial real estate. We seek investors for our projects, and we provide safe, secure returns on their investment in our projects. Our new logo is designed to exhibit strength, class and security, and would like our website to continue on this theme. Our name, Vornelix, is a word-play on a Greek word “aristeia”, which means “excellence” and “a warriors finest moment of glory in war”. If you are in business, you realize that much of it is like war, with strategy and moves and opponents and competitors, and ever-changing economic conditions and threats that make business very much like war. We like to think that we are good at business (war), and so have named our company “Vornelix”, using the founders last name and the word “aristeia” combined. Another definition of "aristeia" is "performing at the peak of one's potential after a long struggle"...again, much like business in real life! The website design should exhibit financial security, smart moves, and positive growth towards a bright future.

Target Market(s)

The target market is smart and wealthy investors, with others such as brokers, cities and government agencies, lenders, sellers, partners, etc also looking at it.

Industry/Entity Type

Investment

Number of Pages Required

5+ page

Font styles to use
Sans Serif

Colors
fec214

Requirements
Must have
• Our website should have a landing page, a "about" or bio page, a projects page and a contact us page. Our new logo uses the colors black and gold, so this should be factored in to our site. The site should be simple, yet impactful and impressive. I have actually two logos, which can be mixed and interchanged in a complimentary way, each with their own unique look.
Nice to have
• I have uploaded a couple screenshots of a website i like, and the simplicity I mention.
Should not have
• The site should not be flashy or complicated or complex or "busy"

```html
<!DOCTYPE html>
<html lang="en">
<head>
<meta charset="utf-8">
<title>Vornelix Capital</title>
<link href="https://fonts.googleapis.com/css2?family=Open+Sans:wght@400;600;700&display=swap" rel="stylesheet">
<style>
:root{
  --gold:#fec214;
  --gold-text:#e9a60c;
  --ink:#333333;
  --muted:#666666;
  --panel:#f0f0f0;
  --dark:#3b3b3b;
  --footer:#3a3a3a;
  --line:#bfbfbf;
  --white:#ffffff;
}
*{box-sizing:border-box;margin:0;padding:0}
html,body{width:1200px;height:2459px;overflow:hidden}
body{font-family:"Open Sans",Arial,sans-serif;color:var(--ink);background:var(--white);position:relative}
.wrap{width:934px;margin:0 auto;position:relative}

/* header */
.site-header{height:134px;border-bottom:5px solid var(--gold);position:relative}
.brand{position:absolute;left:133px;top:50px;display:flex;align-items:center;gap:10px;font-weight:700;font-size:22px;letter-spacing:1px;color:var(--ink)}
.brand .mark{width:22px;height:22px;background:var(--gold)}
.header-mail{position:absolute;right:133px;top:30px;font-size:20px;display:flex;align-items:center;gap:8px}
.main-nav{position:absolute;right:133px;top:82px;display:flex;gap:36px;font-size:14px;color:#555}
.main-nav .active{color:var(--gold-text)}

/* hero */
.hero{height:477px;position:relative;background:linear-gradient(90deg,#e9ebee 0%,#cfd3d8 40%,#6f7580 60%,#2e323b 75%,#b9bec5 100%)}
.hero-title{position:absolute;left:131px;top:300px;font-size:36px;line-height:43px;font-weight:700;color:#3a3a3a;letter-spacing:1px}
.hero-btn{position:absolute;left:134px;top:395px;width:176px;height:43px;background:var(--gold);color:#333;font-weight:700;font-size:16px;display:flex;align-items:center;justify-content:center}
.hero-arrow{position:absolute;top:219px;width:34px;height:34px}
.hero-arrow.prev{left:45px}.hero-arrow.next{left:1120px}

/* services */
.services{height:347px;text-align:center;padding-top:70px}
.section-title{font-size:33px;font-weight:700;color:var(--gold-text);line-height:1}
.services p{width:934px;margin:20px auto 0;font-size:14px;line-height:24.5px;color:#444}
.btn-dark{display:inline-flex;align-items:center;justify-content:center;width:105px;height:36px;background:var(--dark);color:#fff;font-size:13px}
.services .btn-dark{margin-top:22px}

/* projects */
.projects{height:882px;background:var(--panel);text-align:center;padding-top:70px}
.card-grid{display:grid;grid-template-columns:repeat(4,218px);column-gap:20px;row-gap:32px;width:934px;margin:37px auto 0;text-align:left}
.card{height:288px;background:#fff;box-shadow:0 1px 2px rgba(0,0,0,.08)}
.card-photo{height:152px}
.card h3{font-size:14px;font-weight:400;color:#333;padding:12px 10px 0}
.card p{font-size:9.5px;line-height:14px;color:#666;padding:4px 10px 0}
.card .btn-line{display:inline-block;margin:10px 0 0 10px;border:1px solid var(--line);font-size:9.5px;color:#666;padding:5px 10px}
.projects .btn-dark{margin-top:36px;height:34px}

/* contact */
.contact{height:528px;text-align:center;padding-top:90px}
.contact-line{font-size:16px;color:#444;display:flex;justify-content:center;align-items:center;gap:6px}
.contact-line.first{margin-top:18px}
.contact-line.second{margin-top:12px;gap:28px}
.contact-line span{display:inline-flex;align-items:center;gap:6px}
.contact-form{width:934px;margin:22px auto 0}
.field-row{display:grid;grid-template-columns:repeat(4,218px);column-gap:20px}
.field{height:39px;border:1px solid #bbb;font-size:12px;color:#555;text-align:left;padding:11px 14px}
.field.message{height:127px;margin-top:21px}
.contact .btn-dark{margin-top:19px}

/* footer */
.site-footer{position:absolute;left:0;top:2372px;width:1200px;height:87px;background:var(--footer);color:#bbb;font-size:11px}
.footer-links{position:absolute;left:133px;top:22px}
.copyright{position:absolute;left:133px;top:48px}
.social{position:absolute;left:1016px;top:35px;display:flex;gap:22px}
.social i{width:14px;height:14px;border-radius:50%;background:#9a9a9a;display:block}
</style>
</head>
<body>
<header class="site-header">
  <div class="brand"><span class="mark"></span>VORNELIX CAPITAL</div>
  <div class="header-mail">
    <svg width="18" height="14" viewBox="0 0 18 14"><rect width="18" height="14" rx="1" fill="#333"/><path d="M1 1l8 7 8-7" stroke="#fff" stroke-width="1.5" fill="none"/></svg>
    info@vornelixcapital.com
  </div>
  <nav class="main-nav"><span class="active">Welcome</span><span>About Us</span><span>Projects</span><span>Contact</span></nav>
</header>

<section class="hero" role="img" aria-label="Businessman in a dark suit holding a glowing glass skyscraper model over a pale city skyline">
  <h1 class="hero-title">PHASELLUS<br>CONDIMENTUM</h1>
  <div class="hero-btn">GET STARTED NOW</div>
  <svg class="hero-arrow prev" viewBox="0 0 34 34"><circle cx="17" cy="17" r="15" fill="#555" stroke="#fff" stroke-width="2"/><path d="M20 10l-7 7 7 7" stroke="#fff" stroke-width="3" fill="none"/></svg>
  <svg class="hero-arrow next" viewBox="0 0 34 34"><circle cx="17" cy="17" r="15" fill="#222" stroke="#fff" stroke-width="2"/><path d="M14 10l7 7-7 7" stroke="#fff" stroke-width="3" fill="none"/></svg>
</section>

<section class="services">
  <h2 class="section-title">WELCOME TO OUR SERVICES</h2>
  <p>Nam tempus, quam in bibendum vulputate, sapien dolor viverra nisl, vitae euismod elit turpis et nulla. Aliquam erat volutpat. Pellentesque blandit lacus eget nunc faucibus, et tincidunt eros viverra. Phasellus consequat sagittis nisi suscipit feugiat. Cras eget leo sed nunc hendrerit ultricies eu at nisl. Praesent iaculis faucibus urna sit amet lacinia. Maecenas consequat justo enim, ac mattis massa imperdiet quis. Fusce eget neque elit. Sed augue orci, elementum in magna congue, tincidunt vulputate erat. Aliquam consectetur orci molestie dictum molestie.</p>
  <span class="btn-dark">READ MORE</span>
</section>

<section class="projects">
  <h2 class="section-title">PROJECTS</h2>
  <div class="card-grid">
    <article class="card"><div class="card-photo" role="img" aria-label="Suburban family houses with green lawn" style="background:linear-gradient(#7fb0e0,#9aa6b0 55%,#5f8f3a)"></div><h3>Maecenas tortor accumsan</h3><p>Aenean facilisis tincidunt lectus, id dictum luctus eget. Vivamus efficitur condimentum, malesuada eros eget, feugiat nibh.</p><span class="btn-line">Read More</span></article>
    <article class="card"><div class="card-photo" role="img" aria-label="Steel frame building under construction with crane" style="background:linear-gradient(#e6e9ee,#a9b0ba 60%,#6f7680)"></div><h3>Curabitur venenatis</h3><p>Aenean facilisis tincidunt lectus, id dictum luctus eget. Vivamus efficitur condimentum, malesuada eros eget, feugiat nibh.</p><span class="btn-line">Read More</span></article>
    <article class="card"><div class="card-photo" role="img" aria-label="White apartment tower with balconies under blue sky" style="background:linear-gradient(120deg,#3d7fd0,#a9c6e6 50%,#e8ecef)"></div><h3>Etiam mattis augue vehicula</h3><p>Aenean facilisis tincidunt lectus, id dictum luctus eget. Vivamus efficitur condimentum, malesuada eros eget, feugiat nibh.</p><span class="btn-line">Read More</span></article>
    <article class="card"><div class="card-photo" role="img" aria-label="Apartment blocks against a sunlit sky" style="background:linear-gradient(#6f9fd2,#d9b98a 60%,#5a4a3e)"></div><h3>Aliquam erat volutpat</h3><p>Aenean facilisis tincidunt lectus, id dictum luctus eget. Vivamus efficitur condimentum, malesuada eros eget, feugiat nibh.</p><span class="btn-line">Read More</span></article>
    <article class="card"><div class="card-photo" role="img" aria-label="Modern residential complex with garden at sunset" style="background:linear-gradient(#e8b27a,#8a6f58 55%,#5e7a3a)"></div><h3>Cras sollicitudin cursus</h3><p>Aenean facilisis tincidunt lectus, id dictum luctus eget. Vivamus efficitur condimentum, malesuada eros eget, feugiat nibh.</p><span class="btn-line">Read More</span></article>
    <article class="card"><div class="card-photo" role="img" aria-label="White modern villa with swimming pool" style="background:linear-gradient(#6aa8e0,#dfe6ea 55%,#3aa0c8)"></div><h3>Vivamus lacus justo, ultrices</h3><p>Aenean facilisis tincidunt lectus, id dictum luctus eget. Vivamus efficitur condimentum, malesuada eros eget, feugiat nibh.</p><span class="btn-line">Read More</span></article>
    <article class="card"><div class="card-photo" role="img" aria-label="Lit glass office buildings at dusk" style="background:linear-gradient(#2a4fb0,#3a5ab8 50%,#d99a3a)"></div><h3>Pellentesque convalli</h3><p>Aenean facilisis tincidunt lectus, id dictum luctus eget. Vivamus efficitur condimentum, malesuada eros eget, feugiat nibh.</p><span class="btn-line">Read More</span></article>
    <article class="card"><div class="card-photo" role="img" aria-label="Terrace with infinity pool overlooking the sea" style="background:linear-gradient(#9ec7e6,#d6e0e6 50%,#2a5f80)"></div><h3>Cras augue magna, placera</h3><p>Aenean facilisis tincidunt lectus, id dictum luctus eget. Vivamus efficitur condimentum, malesuada eros eget, feugiat nibh.</p><span class="btn-line">Read More</span></article>
  </div>
  <span class="btn-dark">VIEW ALL</span>
</section>

<section class="contact">
  <h2 class="section-title">CONTACT US</h2>
  <div class="contact-line first">
    <svg width="10" height="14" viewBox="0 0 10 14"><path d="M5 0a5 5 0 0 0-5 5c0 4 5 9 5 9s5-5 5-9a5 5 0 0 0-5-5z" fill="#444"/><circle cx="5" cy="5" r="2" fill="#fff"/></svg>
    24 Building name, Street name, City Zipcode
  </div>
  <div class="contact-line second">
    <span><svg width="13" height="13" viewBox="0 0 13 13"><path d="M3 0l2 3-1.5 1.5a8 8 0 0 0 5 5L10 8l3 2-1.5 2.5C6 13 0 7 .5 1.5z" fill="#444"/></svg>Phone : 555 013 2847</span>
    <span><svg width="15" height="11" viewBox="0 0 15 11"><rect width="15" height="11" rx="1" fill="#444"/><path d="M1 1l6.5 5.5L14 1" stroke="#fff" stroke-width="1.3" fill="none"/></svg>Email : info@vornelixcapital.com</span>
  </div>
  <form class="contact-form">
    <div class="field-row">
      <div class="field">Name</div><div class="field">Email</div><div class="field">Phone</div><div class="field">City</div>
    </div>
    <div class="field message">Message</div>
  </form>
  <span class="btn-dark">SUBMIT</span>
</section>

<footer class="site-footer">
  <div class="footer-links">Welcome &nbsp; | &nbsp; About Us &nbsp; | &nbsp; Projects &nbsp; | &nbsp; Contact</div>
  <div class="copyright">Copyright © &nbsp;2018 &nbsp;Vornelix capital. &nbsp;All rights reserved.</div>
  <div class="social"><i></i><i></i></div>
</footer>
</body>
</html>
```